Equipment Finance Specialist I work with companies who need the funds to buy their equipment

I would like a business card that stands out on the shelves. I want to be able to hand it to someone and say WOW. This card should have my logo.
You can put color into it I am very open on design and color

What my company does is we deal with dealerships that sell equipment such as Dump Trucks garbage trucks tractors trailers. Customers get referred to us and depending on their time in business we will ask for the following items

Companies that have been in business for more than two years we have a credit application program up to 250K . With this program we need the following items Credit application filled out(which is what I would like to be able for the customer to click on my website to get.) as well as three current month bank statements.

Deals over 250k we will need the following items

2 years business tax returns
2 years personal tax returns
Profit & Loss statement
Personal Financial Statement

what we do
100% FINANCING
SEASONAL PAYMENTS
LOAN BALLOON PAYMENTS
TRAC LEASING
LOW-INTEREST REFINANCING RATES
DEBT CONSOLIDATION

We specialize in creative financing solutions and offer a variety of reliable, flexible and expandable lending choices.

Target Market(s)

Trucking Companies

Industry/Entity Type

Trucking Company

Contact Information for Business Card

* $250,000 Application only Program
* Loans from $30,000 to 5,000,000
* Competitive Interest Rates

Font styles to use
Serif
Sans Serif

Colors

Designer to choose colors to be used in the design.

Requirements
Must have
• On the back of the card.
• * $250,000 Application only Program
• * Loans from $30,000 to 5,000,000
• My name, email, website. address
• * Competitive Interest Rates
• * 100% Financing
Nice to have
• I want my logo to pop on the card
• My logo is the great one I would like to use
Should not have
• I am up for your creativity as well

```html
<!DOCTYPE html>
<html lang="en">
<head>
<meta charset="utf-8">
<title>Summit Lending – Business Card</title>
<link rel="stylesheet" href="https://fonts.googleapis.com/css2?family=Source+Sans+3:ital,wght@0,400;0,600;0,700;1,600&display=swap">
<style>
  :root {
    --backdrop: #5c5c5c;
    --navy: #0d2a6e;
    --navy-deep: #0a2565;
    --red: #d2141f;
    --ink: #2b2b2b;
    --rule: #a9a9a9;
    --paper: #ffffff;
    --back-rule: rgba(255,255,255,0.45);
    --back-muted: #c9d2e6;
  }
  * { box-sizing: border-box; margin: 0; padding: 0; }
  html, body {
    width: 1200px; height: 802px; overflow: hidden;
    background: var(--backdrop);
    font-family: "Source Sans 3", sans-serif;
  }
  .card {
    position: absolute; top: 233px;
    width: 560px; height: 335px;
    box-shadow: 0 4px 10px rgba(0,0,0,0.35);
  }
  .card-front { left: 25px; background: var(--paper); color: var(--ink); }
  .card-back { left: 615px; background: var(--navy-deep); color: #fff; text-align: center; }

  /* front */
  .brand {
    position: absolute; left: 30px; top: 142px;
    display: flex; align-items: center; gap: 10px;
    font-weight: 700; font-size: 25px; color: var(--navy); letter-spacing: 0.5px;
  }
  .brand-dot { width: 34px; height: 34px; border-radius: 50%; background: var(--navy); }
  .front-divider {
    position: absolute; left: 280px; top: 82px; width: 1px; height: 150px; background: #cfcfcf;
  }
  .person { position: absolute; left: 301px; top: 78px; }
  .person-name { font-weight: 700; font-size: 22px; color: var(--navy); letter-spacing: 0.5px; line-height: 1; }
  .person-role { font-size: 15px; color: var(--red); margin-top: 2px; }
  .contact-list { list-style: none; margin-top: 6px; font-size: 15px; line-height: 20px; }
  .contact-list li { display: flex; align-items: center; gap: 5px; }
  .contact-list svg { width: 13px; height: 13px; fill: var(--navy); flex: none; }
  .address { font-size: 15px; line-height: 20px; margin-top: 5px; }
  .front-rule {
    position: absolute; left: 48px; top: 253px; width: 452px; height: 1px; background: var(--rule);
  }
  .highlights {
    position: absolute; left: 46px; top: 263px;
    display: grid; grid-template-columns: 266px auto; row-gap: 0;
    list-style: none; font-size: 15px; line-height: 20px;
  }
  .highlights li { display: flex; align-items: center; gap: 6px; white-space: nowrap; }
  .highlights li::before {
    content: ""; width: 6px; height: 6px; border-radius: 50%; background: var(--red);
  }

  /* back */
  .requirements { position: absolute; left: 0; right: 0; top: 80px; font-size: 17.5px; line-height: 25px; }
  .requirements .sep { margin: 0 8px; }
  .section-title {
    position: absolute; left: 55px; right: 55px; top: 152px;
    display: flex; align-items: center; gap: 10px;
    font-weight: 600; font-size: 15px; color: var(--back-muted);
  }
  .section-title::before, .section-title::after {
    content: ""; flex: 1; height: 1px; background: var(--back-rule);
  }
  .services {
    position: absolute; left: 0; right: 0; top: 182px;
    font-size: 13.5px; line-height: 17px; text-transform: uppercase; white-space: nowrap;
  }
  .services .dot {
    display: inline-block; width: 6px; height: 6px; border-radius: 50%;
    background: #fff; margin: 0 10px; vertical-align: middle;
  }
  .back-rule {
    position: absolute; left: 55px; right: 55px; top: 240px; height: 1px; background: var(--back-rule);
  }
  .tagline {
    position: absolute; left: 0; right: 0; top: 254px;
    font-style: italic; font-weight: 600; font-size: 16px; line-height: 20px;
  }
</style>
</head>
<body>

<section class="card card-front">
  <div class="brand"><span class="brand-dot"></span>SUMMIT LENDING</div>
  <div class="front-divider"></div>
  <div class="person">
    <p class="person-name">DANIEL HARPER</p>
    <p class="person-role">Managing Director</p>
    <ul class="contact-list">
      <li><svg viewBox="0 0 16 16"><path d="M3 2h3l1 4-2 1a9 9 0 0 0 4 4l1-2 4 1v3a1 1 0 0 1-1 1A13 13 0 0 1 2 3a1 1 0 0 1 1-1z"/></svg>055-987 654 321</li>
      <li><svg viewBox="0 0 16 16"><path d="M1 3h14v10H1z M2 4v1l6 4 6-4V4z" fill-rule="evenodd"/></svg>hello@summitlend.example</li>
      <li><svg viewBox="0 0 16 16"><circle cx="8" cy="8" r="7"/></svg>www.summitlend.example</li>
    </ul>
    <p class="address">218 Ridgeway Drive,<br>60714, Northland</p>
  </div>
  <div class="front-rule"></div>
  <ul class="highlights">
    <li>$250,000 Application only Program</li>
    <li>Competitive Interest Rates</li>
    <li>Loans from $30,000 to 5,000,000</li>
    <li>100% Financing</li>
  </ul>
</section>

<section class="card card-back">
  <div class="requirements">
    <p>2 years business tax returns<span class="sep">|</span>2 years personal tax returns</p>
    <p>Profit &amp; Loss statement<span class="sep">|</span>Personal Financial Statement</p>
  </div>
  <h2 class="section-title">WHAT WE DO</h2>
  <div class="services">
    <p>100% Financing<span class="dot"></span>Seasonal Payments<span class="dot"></span>Loan Balloon Payments</p>
    <p>TRAC Leasing<span class="dot"></span>Low-Interest Refinancing Rates<span class="dot"></span>Debt Consolidation</p>
  </div>
  <div class="back-rule"></div>
  <p class="tagline">We specialize in creative financing solutions and offer<br>a variety of reliable, flexible and expandable lending choices.</p>
</section>

</body>
</html>
```